Verodex business card

Business card for sustainable investment company called "Verodex". Verodex is an exchange platform selling carbon credits between buyers and sellers. Carbon Credits are an environmental commodity for reducing global carbon emissions.

the card should obviously have our logo and the theme should be sustainability/environment mixed with a trading platform.

Contact Information for Business Card

Logo, Name, Title, Phone, Email

Colors
0054AA
0677BA
7BADD7
CADEEF
E8F1F8
0094D4
00A9DD
6FCCEA
C7EBF8
E9F6FB
00AB8E
00BBA5
67D7C9
C6EFE9
E9F9F6
59FF00
82FF00
B8FF75
E3FFCB
F4FFEA

```html
<!DOCTYPE html>
<html lang="en">
<head>
<meta charset="UTF-8">
<title>Verodex Business Card</title>
<link rel="stylesheet" href="https://fonts.googleapis.com/css2?family=Open+Sans:wght@400;600;700&display=swap">
<style>
  :root {
    --stage: #333333;
    --navy: #14294f;
    --front-cyan: #67cddb;
    --front-blue: #4a77c0;
    --emboss: #4f9cc9;
    --accent-teal: #4fb6d3;
    --accent-blue: #5b8fd0;
    --icon-blue: #5fb4dc;
    --white: #ffffff;
  }
  * { box-sizing: border-box; margin: 0; padding: 0; }
  html, body {
    width: 1200px; height: 780px; overflow: hidden;
    background: var(--stage);
    font-family: "Open Sans", Arial, sans-serif;
  }
  .sheet {
    position: relative; width: 1200px; height: 780px;
    display: flex; align-items: center; justify-content: center; gap: 48px;
  }
  .card {
    position: relative; width: 546px; height: 312px; overflow: hidden;
    box-shadow: 0 10px 24px rgba(0,0,0,0.45);
  }

  /* Front side */
  .card-front {
    background: linear-gradient(35deg, var(--front-cyan) 0%, #5fb0d4 45%, var(--front-blue) 100%);
    display: flex; align-items: center; justify-content: center; gap: 14px;
  }
  .front-mark {
    width: 26px; height: 26px; background: var(--emboss);
  }
  .front-wordmark {
    font-weight: 700; font-size: 52px; letter-spacing: 2px;
    color: var(--emboss); text-transform: uppercase;
  }

  /* Back side */
  .card-back { background: var(--navy); color: var(--white); }
  .back-logo {
    position: absolute; left: 34px; top: 70px;
    display: flex; align-items: center; gap: 12px;
  }
  .back-logo-mark { width: 22px; height: 22px; background: var(--accent-blue); }
  .back-wordmark {
    font-weight: 700; font-size: 34px; letter-spacing: 1px;
    color: var(--white); text-transform: uppercase;
  }
  .person {
    position: absolute; right: 40px; top: 26px; text-align: right;
  }
  .person-name {
    font-weight: 700; font-size: 26px; letter-spacing: 1px; color: var(--accent-teal);
    line-height: 1.15;
  }
  .person-title { font-weight: 600; font-size: 15px; letter-spacing: 0.5px; }
  .edge-bar {
    position: absolute; right: 14px; top: 22px; width: 12px; height: 54px;
    background: linear-gradient(180deg, var(--accent-blue), var(--accent-teal));
  }
  .address {
    position: absolute; left: 42px; top: 176px;
    font-size: 15px; line-height: 1.35; letter-spacing: 0.4px;
  }
  .contacts {
    position: absolute; left: 42px; top: 226px; list-style: none;
    font-size: 15px; line-height: 1.35; letter-spacing: 0.4px;
  }
  .contacts li { display: flex; align-items: center; gap: 10px; }
  .contacts svg { width: 14px; height: 14px; flex: none; }
</style>
</head>
<body>
<main class="sheet">
  <section class="card card-front" aria-label="Card front">
    <span class="front-mark" aria-hidden="true"></span>
    <span class="front-wordmark">Verodex</span>
  </section>

  <section class="card card-back" aria-label="Card back">
    <div class="edge-bar" aria-hidden="true"></div>
    <div class="person">
      <p class="person-name">Lena Havlova</p>
      <p class="person-title">Managing Director</p>
    </div>

    <div class="back-logo">
      <span class="back-logo-mark" aria-hidden="true"></span>
      <span class="back-wordmark">Verodex</span>
    </div>

    <address class="address" style="font-style:normal">
      418 Meridian Ave. Suite 120<br>
      Dallas, TX 75201
    </address>

    <ul class="contacts">
      <li>
        <svg viewBox="0 0 24 24" aria-hidden="true"><path fill="#5fb4dc" d="M6.6 10.8a15.1 15.1 0 0 0 6.6 6.6l2.2-2.2c.3-.3.7-.4 1-.2 1.1.4 2.3.6 3.6.6.6 0 1 .4 1 1V20c0 .6-.4 1-1 1A17 17 0 0 1 3 4c0-.6.4-1 1-1h3.5c.6 0 1 .4 1 1 0 1.3.2 2.5.6 3.6.1.3 0 .7-.2 1z"/></svg>
        <span>(555) 014-3920</span>
      </li>
      <li>
        <svg viewBox="0 0 24 24" aria-hidden="true"><rect x="2" y="5" width="20" height="14" rx="1.5" fill="none" stroke="#5fb4dc" stroke-width="2"/><path d="M3 6l9 7 9-7" fill="none" stroke="#5fb4dc" stroke-width="2"/></svg>
        <span>info@verodex.com</span>
      </li>
      <li>
        <svg viewBox="0 0 24 24" aria-hidden="true"><circle cx="12" cy="12" r="9.5" fill="none" stroke="#5fb4dc" stroke-width="2"/><ellipse cx="12" cy="12" rx="4" ry="9.5" fill="none" stroke="#5fb4dc" stroke-width="1.6"/><path d="M2.5 12h19" stroke="#5fb4dc" stroke-width="1.6"/></svg>
        <span>www.verodex.com</span>
      </li>
    </ul>
  </section>
</main>
</body>
</html>
```